Plumbing company needs Business Card Design

Hi I need business card design based on logo which I uploaded. Its plumbing and heating company called Kranex Usługi Hydrauliczno-Gazowe. I want to see on my card motto of my company which is "...od wymiany uszczelki po wymiane łazienki.", my phone number, name, and website: 612478390, Marek Olejnik, info@kranex-inst.org, www.kranex-inst.org
I want to see logos of companys which I'm approved installer (Termova) (Le Valmont) (Korvo) (Plumox).
I want new creative look of business card. I like rounded corners.
Any questions please send message.
Thanks for intrest.
Industry/Entity Type
Business
Contact Information for Business Card
Marek Olejnik
612 478 390
info@kranex-inst.org
www.kranex-inst.org
...od wymiany uszczelki po wymiane łazienki.

```html
<!DOCTYPE html>
<html lang="pl">
<head>
<meta charset="utf-8">
<title>Kranex – wizytówki</title>
<link rel="stylesheet" href="https://fonts.googleapis.com/css2?family=Montserrat:wght@500;600;700;800&family=Oswald:wght@500&display=swap">
<style>
:root{
  --bg:#2b2b2d;
  --paper:#f4f4f4;
  --navy:#1c3a7c;
  --red:#d0111b;
  --yellow:#f6e600;
  --ink:#333a48;
  --ghost:rgba(120,125,135,.13);
  --ghost-dark:rgba(255,255,255,.08);
}
*{margin:0;padding:0;box-sizing:border-box}
html,body{width:1200px;height:1000px;overflow:hidden}
body{background:var(--bg);font-family:"Montserrat",sans-serif;position:relative}
.card{position:absolute;width:443px;height:282px;border-radius:12px;overflow:hidden;background:var(--paper);box-shadow:0 6px 14px rgba(0,0,0,.45)}
.card--front{left:115px;top:215px}
.card--back{left:651px;top:215px}
.card--partners{left:366px;top:570px;background:var(--navy)}
.mascot{position:absolute;left:250px;top:38px;width:200px;height:200px;border-radius:50%;background:var(--ghost)}
.card--partners .mascot{left:240px;top:20px;background:var(--ghost-dark)}
.brand{position:absolute;left:34px;top:31px;display:flex;align-items:center;gap:10px}
.brand__mark{width:70px;height:70px;border-radius:9px;background:var(--yellow);border:4px solid var(--red)}
.brand__name{font-weight:800;font-size:38px;line-height:1;color:var(--red)}
.brand__tagline{font-family:"Oswald",sans-serif;font-weight:500;font-size:14px;color:var(--navy);margin-top:4px}
.card--partners .brand__tagline{color:#fff}
.person{position:absolute;font-weight:700;font-size:18px;letter-spacing:.5px;color:var(--navy);text-transform:uppercase}
.card--front .person{left:33px;top:158px}
.card--back .person{left:29px;top:161px}
.icon{width:15px;height:15px;border-radius:3px;background:var(--red);display:inline-flex;align-items:center;justify-content:center;flex:none}
.icon svg{width:11px;height:11px}
.stripe{position:absolute;left:0;width:100%}
.stripe--red{top:217px;height:5px;background:var(--red)}
.stripe--navy{top:222px;height:60px;background:var(--navy);display:flex;align-items:center;gap:10px;padding-left:24px;color:#fff;font-size:11.5px;font-weight:500;white-space:nowrap}
.contact-item{display:flex;align-items:center;gap:5px;white-space:nowrap}
.contact-list{position:absolute;left:30px;top:196px;list-style:none;font-size:12.5px;font-weight:500;color:var(--ink);white-space:nowrap}
.contact-list li{display:flex;align-items:center;gap:8px;height:19.5px}
.motto{position:absolute;left:196px;top:227px;width:234px;height:24px;border-radius:12px;background:var(--navy);color:#fff;font-size:8.2px;font-weight:700;white-space:nowrap;display:flex;align-items:center;justify-content:center;padding:0 6px}
.hotline{position:absolute;left:32px;top:131px;display:flex;align-items:center;gap:10px;color:#fff;font-size:22px;font-weight:500}
.hotline .icon{width:18px;height:18px}
.partners{position:absolute;left:0;top:180px;width:100%;height:67px;background:var(--paper);display:flex;align-items:center;justify-content:space-around;padding:0 16px}
.partner{font-weight:700;font-size:17px;color:var(--navy)}
.partners-base{position:absolute;left:0;top:247px;width:100%;height:35px;background:var(--red)}
</style>
</head>
<body>

<!-- front card -->
<section class="card card--front">
  <div class="mascot" role="img" aria-label="Faint plumber mascot decoration"></div>
  <div class="brand">
    <div class="brand__mark"></div>
    <div><div class="brand__name">Kranex</div><div class="brand__tagline">Usługi Hydrauliczno-Gazowe</div></div>
  </div>
  <p class="person">Marek Olejnik</p>
  <div class="stripe stripe--red"></div>
  <div class="stripe stripe--navy">
    <span class="contact-item"><span class="icon"><svg viewBox="0 0 24 24"><path fill="#fff" d="M6.6 10.8a15 15 0 0 0 6.6 6.6l2.2-2.2c.3-.3.7-.4 1-.2 1.1.4 2.3.6 3.6.6.6 0 1 .4 1 1V20c0 .6-.4 1-1 1A17 17 0 0 1 3 4c0-.6.4-1 1-1h3.5c.6 0 1 .4 1 1 0 1.3.2 2.5.6 3.6.1.3 0 .7-.2 1z"/></svg></span>612478390</span>
    <span class="contact-item"><span class="icon"><svg viewBox="0 0 24 24"><rect x="3" y="6" width="18" height="12" fill="none" stroke="#fff" stroke-width="2"/><path d="M3 6l9 7 9-7" fill="none" stroke="#fff" stroke-width="2"/></svg></span>info@kranex-inst.org</span>
    <span class="contact-item"><span class="icon"><svg viewBox="0 0 24 24"><circle cx="12" cy="12" r="9" fill="none" stroke="#fff" stroke-width="2"/><path d="M3 12h18M12 3c3 3 3 15 0 18M12 3c-3 3-3 15 0 18" fill="none" stroke="#fff" stroke-width="1.6"/></svg></span>www.kranex-inst.org</span>
  </div>
</section>

<!-- back card -->
<section class="card card--back">
  <div class="mascot" role="img" aria-label="Faint plumber mascot decoration"></div>
  <div class="brand">
    <div class="brand__mark"></div>
    <div><div class="brand__name">Kranex</div><div class="brand__tagline">Usługi Hydrauliczno-Gazowe</div></div>
  </div>
  <p class="person">Marek Olejnik</p>
  <ul class="contact-list">
    <li><span class="icon"><svg viewBox="0 0 24 24"><path fill="#fff" d="M6.6 10.8a15 15 0 0 0 6.6 6.6l2.2-2.2c.3-.3.7-.4 1-.2 1.1.4 2.3.6 3.6.6.6 0 1 .4 1 1V20c0 .6-.4 1-1 1A17 17 0 0 1 3 4c0-.6.4-1 1-1h3.5c.6 0 1 .4 1 1 0 1.3.2 2.5.6 3.6.1.3 0 .7-.2 1z"/></svg></span>612478390</li>
    <li><span class="icon"><svg viewBox="0 0 24 24"><rect x="3" y="6" width="18" height="12" fill="none" stroke="#fff" stroke-width="2"/><path d="M3 6l9 7 9-7" fill="none" stroke="#fff" stroke-width="2"/></svg></span>info@kranex-inst.org</li>
    <li><span class="icon"><svg viewBox="0 0 24 24"><circle cx="12" cy="12" r="9" fill="none" stroke="#fff" stroke-width="2"/><path d="M3 12h18M12 3c3 3 3 15 0 18M12 3c-3 3-3 15 0 18" fill="none" stroke="#fff" stroke-width="1.6"/></svg></span>www.kranex-inst.org</li>
  </ul>
  <p class="motto">...od wymiany uszczelki po wymiane łazienki</p>
</section>

<!-- partners card -->
<section class="card card--partners">
  <div class="mascot" role="img" aria-label="Faint plumber mascot decoration"></div>
  <div class="brand">
    <div class="brand__mark"></div>
    <div><div class="brand__name">Kranex</div><div class="brand__tagline">Usługi Hydrauliczno-Gazowe</div></div>
  </div>
  <div class="hotline"><span class="icon"><svg viewBox="0 0 24 24"><path fill="#fff" d="M6.6 10.8a15 15 0 0 0 6.6 6.6l2.2-2.2c.3-.3.7-.4 1-.2 1.1.4 2.3.6 3.6.6.6 0 1 .4 1 1V20c0 .6-.4 1-1 1A17 17 0 0 1 3 4c0-.6.4-1 1-1h3.5c.6 0 1 .4 1 1 0 1.3.2 2.5.6 3.6.1.3 0 .7-.2 1z"/></svg></span>612 478 390</div>
  <div class="partners">
    <span class="partner">Termova</span>
    <span class="partner">Korvo</span>
    <span class="partner">Le Valmont</span>
    <span class="partner">Plumox</span>
  </div>
  <div class="partners-base"></div>
</section>

</body>
</html>
```